Veldmark Supplies Business Card

Professional business card that stand out to our potential customers. Front and back with clean modern design

Industry/Entity Type

Oil and gas

Contact Information for Business Card

Name, address, website , office phone and cell number

Requirements
Must have
• Editable files for each employee

```html
<!DOCTYPE html>
<html lang="en">
<head>
<meta charset="utf-8">
<title>Veldmark Supplies Business Card</title>
<link href="https://fonts.googleapis.com/css2?family=Montserrat:wght@400;500;700;800&display=swap" rel="stylesheet">
<style>
  :root {
    --bg: #adadad;
    --card-dark: #1c1816;
    --card-light: #ffffff;
    --red: #ee2325;
    --blue: #08afd0;
    --ink: #111111;
    --text: #555555;
    --white: #ffffff;
  }
  * { margin: 0; padding: 0; box-sizing: border-box; }
  html, body { width: 1200px; height: 1000px; overflow: hidden; }
  body { background: var(--bg); font-family: "Montserrat", sans-serif; position: relative; }

  .card { position: absolute; left: 252px; width: 695px; height: 400px; border-radius: 22px; overflow: hidden; }

  .card--front { top: 92px; background: var(--card-dark); }
  .front-art {
    position: absolute; left: 0; top: 0; width: 440px; height: 400px;
    background: radial-gradient(ellipse at 45% 45%, #7a3a35 0%, #4a2826 40%, var(--card-dark) 75%);
  }
  .front-url { position: absolute; left: 377px; top: 320px; font-size: 24px; font-weight: 400; color: var(--white); letter-spacing: -0.2px; }
  .front-url .red { color: var(--red); font-weight: 700; }
  .front-url .blue { color: var(--blue); font-weight: 700; }

  .card--back { top: 547px; background: var(--card-light); }
  .brand { position: absolute; left: 57px; top: 178px; width: 228px; display: flex; align-items: center; gap: 10px; }
  .brand-mark { width: 26px; height: 26px; background: var(--red); flex: none; }
  .brand-name { font-size: 22px; font-weight: 800; color: var(--red); white-space: nowrap; }

  .details { position: absolute; left: 341px; top: 92px; }
  .person-name { font-size: 30px; font-weight: 800; line-height: 1; letter-spacing: -0.3px; }
  .person-name .first { color: var(--red); }
  .person-name .last { color: var(--blue); }
  .position { margin-top: 6px; font-size: 14px; font-weight: 700; letter-spacing: 1.2px; color: var(--ink); }
  .address { margin-top: 14px; font-size: 17px; line-height: 19px; color: var(--text); }
  .contacts { list-style: none; margin-top: 14px; }
  .contacts li { display: flex; align-items: center; gap: 10px; font-size: 17px; color: var(--text); height: 28px; }
  .contacts svg { width: 15px; height: 15px; flex: none; }

  .band { position: absolute; left: 0; bottom: 0; width: 695px; height: 32px; }
</style>
</head>
<body>
  <section class="card card--front">
    <div class="front-art" role="img" aria-label="Large decorative brand emblem in red and teal, softly blurred"></div>
    <p class="front-url"><span class="red">veldmark</span><span class="blue">supplies</span>.com</p>
  </section>

  <section class="card card--back">
    <div class="brand">
      <span class="brand-mark"></span>
      <span class="brand-name">Veldmark Supplies</span>
    </div>

    <div class="details">
      <h1 class="person-name"><span class="first">Name</span> <span class="last">Surname</span></h1>
      <p class="position">POSITION</p>
      <p class="address">412 N.Calloway Suite 5<br>Midvale, Tx 79710</p>
      <ul class="contacts">
        <li>
          <svg viewBox="0 0 16 16"><rect x="4" y="1" width="8" height="14" rx="1.5" fill="none" stroke="var(--blue)" stroke-width="1.6"/><circle cx="8" cy="12.5" r="0.9" fill="var(--blue)"/></svg>
          (555) 284-0193
        </li>
        <li>
          <svg viewBox="0 0 16 16"><rect x="1" y="4" width="14" height="9" fill="var(--blue)"/><path d="M1 4 L8 9.5 L15 4" fill="none" stroke="#fff" stroke-width="1.2"/></svg>
          sales@veldmarksupplies.com
        </li>
        <li>
          <svg viewBox="0 0 16 16"><circle cx="8" cy="8.5" r="6" fill="var(--blue)"/><path d="M2 8.5 H14 M8 2.5 V14.5 M3.2 5.5 H12.8 M3.2 11.5 H12.8" stroke="#fff" stroke-width="0.8" fill="none"/><ellipse cx="8" cy="8.5" rx="2.8" ry="6" fill="none" stroke="#fff" stroke-width="0.8"/></svg>
          veldmarksupplies.com
        </li>
      </ul>
    </div>

    <svg class="band" viewBox="0 0 695 32" preserveAspectRatio="none">
      <polygon points="0,0 292,0 280,32 0,32" fill="var(--red)"/>
      <polygon points="301,0 695,0 695,32 289,32" fill="var(--blue)"/>
    </svg>
  </section>
</body>
</html>
```